Web Design

We need a website for a company based in Doha Qatar called
Lumara Maid Service.

It is the number one maid cleaning service company, and we have branches all over qatar.

Luxury Cleaning Service Provider.

The color scheme is gold, yellow and black like the logo.

Before they get to the website, there is an intro video.

The website should depict luxury.

Target Market(s)

People who need maids at their houses.

Industry/Entity Type

Cleaning Service

Requirements
Must have
• Luxury, Sleek, Modern

The opening sequence is a video which I already have. Its too big to upload here so I am going to put it on youtube.

After the opening sequence, the home page should have a widescreen photo background and it should change every five seconds, the first background photo should be of qatar westbay skyline. Then the second background should be of maid photos in cleaning positions. Then the third background should be of cleaner photos etc.

We will send you all the tabs and all the content later.

```html
<!DOCTYPE html>
<html lang="en">
<head>
<meta charset="utf-8">
<title>Lumara Maid Service</title>
<link href="https://fonts.googleapis.com/css2?family=Mada:wght@400;500;600;700&family=Ubuntu:wght@400;500;700&display=swap" rel="stylesheet">
<style>
:root{
  --gold-light:#f7d66a;
  --gold:#e8b930;
  --gold-deep:#c9962a;
  --gold-text:#d19a1a;
  --brown-black:#1e0f08;
  --logo-black:#150b05;
  --ink:#2b2b2b;
  --body-ink:#3c3c3c;
  --white:#ffffff;
  --sky-top:#8d8d8d;
  --sky-bottom:#3a3a3a;
}
*{margin:0;padding:0;box-sizing:border-box}
html,body{width:674px;height:1200px;overflow:hidden;background:var(--white)}
body{position:relative;font-family:"Mada",sans-serif;color:var(--body-ink)}

.hero{position:absolute;left:0;top:0;width:674px;height:370px;
  background:linear-gradient(180deg,#9a9a9a 0%,#6f6f6f 55%,#4a4a4a 75%,#2f2f2f 100%);
  border-top:3px solid #5a3a14}
.nav-bar{position:absolute;top:3px;height:62px;
  background:linear-gradient(180deg,var(--gold-light) 0%,var(--gold) 60%,var(--gold-deep) 100%);
  display:flex;align-items:center;justify-content:space-around;padding:0 14px;
  box-shadow:0 2px 4px rgba(0,0,0,.35)}
.nav-left{left:67px;width:211px}
.nav-right{left:396px;width:210px}
.nav-bar a{font-family:"Mada",sans-serif;font-weight:700;font-size:8.4px;color:#3a2308;text-decoration:none;letter-spacing:.2px}
.logo-block{position:absolute;left:278px;top:0;width:118px;height:94px;background:var(--logo-black);
  display:flex;align-items:center;justify-content:center;box-shadow:0 2px 6px rgba(0,0,0,.5)}
.logo-name{font-family:"Mada",sans-serif;font-weight:600;font-size:10px;color:var(--gold);letter-spacing:.5px}

.slider{position:absolute;left:67px;top:75px;width:539px;height:262px;
  background:linear-gradient(110deg,#d9c7a3 0%,#efe6d6 35%,#f6f2ea 60%,#cfc2aa 100%)}
.slider-dots{position:absolute;left:312px;top:316px;display:flex;gap:3px}
.slider-dots span{width:10px;height:10px;border-radius:50%;background:var(--white);border:1px solid #bbb}
.slider-dots span.active{background:#111;border-color:#111}

.section-title{position:absolute;left:67px;top:388px;font-family:"Ubuntu",sans-serif;font-weight:700;font-size:10.4px;color:var(--gold-text);letter-spacing:.3px}
.lead{position:absolute;left:67px;top:414px;font-family:"Ubuntu",sans-serif;font-size:10.6px;color:#111}
.intro{position:absolute;left:67px;top:430px;width:540px;font-size:7.6px;line-height:13.5px;color:var(--body-ink)}

.service{position:absolute;width:256px}
.service-photo{width:256px;height:132px;border:1px solid #ddd}
.service-name{margin-top:12px;font-family:"Ubuntu",sans-serif;font-weight:500;font-size:10.4px;color:#1a1a1a}
.service-text{position:absolute;top:172px;left:0;width:256px;font-size:7.6px;line-height:13.6px;color:var(--body-ink)}
.btn{position:absolute;left:0;width:67px;height:23px;display:flex;align-items:center;justify-content:center;
  background:linear-gradient(180deg,var(--gold-light),var(--gold) 60%,var(--gold-deep));
  font-family:"Mada",sans-serif;font-weight:600;font-size:7.8px;color:#3a2308;text-decoration:none;
  box-shadow:0 1px 2px rgba(0,0,0,.25)}

.footer{position:absolute;left:0;top:1138px;width:674px;height:62px;background:var(--brown-black)}
.footer-links{position:absolute;left:73px;top:19px;display:flex;align-items:center;font-size:8px;font-weight:500;color:var(--white)}
.footer-links a{color:var(--white);text-decoration:none}
.footer-links .sep{margin:0 9px}
.copyright{position:absolute;left:73px;top:37px;font-size:7.8px;font-weight:500;color:var(--white)}
.social{position:absolute;left:588px;top:23px;width:16px;height:16px}
</style>
</head>
<body>

<header class="hero" role="img" aria-label="Black and white photo of the West Bay skyline with cranes and water">
</header>

<nav class="nav-bar nav-left">
  <a href="#">HOME</a><a href="#">ABOUT US</a><a href="#">SERVICES</a><a href="#">TEAM</a>
</nav>
<div class="logo-block"><span class="logo-name">Lumara Maid</span></div>
<nav class="nav-bar nav-right">
  <a href="#">LOCATIONS</a><a href="#">TESTIMONIALS</a><a href="#">CONTACT US</a>
</nav>

<div class="slider" role="img" aria-label="Photo of a maid arranging pillows on a cream sofa"></div>
<div class="slider-dots"><span class="active"></span><span></span><span></span><span></span></div>

<h2 class="section-title">SERVICES</h2>
<p class="lead">Providing a quality cleaning service with attention to detail!!!</p>
<p class="intro">Our cleaning services are thorough, consistent and customized. Every office and home is different and our cleaning services are always designed around your home's/your company's particular needs. We understand the concerns of our customers and we work diligently to provide tiptop cleaning services for your home or company while maintaining the Health &amp; Safety and Security of your home/office. There will be a sense of great accomplishment when LMS leaves a place looking and smelling CLEAN!</p>

<article class="service" style="left:67px;top:500px">
  <div class="service-photo" role="img" aria-label="Photo of a woman in gloves wiping a kitchen counter" style="background:linear-gradient(120deg,#b9c99a,#e6c9a0 45%,#d8a86e 80%,#b8763e)"></div>
  <h3 class="service-name">Regular Cleaning</h3>
  <p class="service-text">Bedrooms, Kitchen, Bathrooms, Living Areas including Hallways and stairs.On every visit, our LMS team dusts, vacuums, washes and sanitizes each room. Areas on which you want us to focus first and we will work through all areas of your home according to your priority.Booking: We recommend clients to book cleaning services on any fixed days during the week which will be followed</p>
  <a class="btn" href="#" style="top:260px">Read More</a>
</article>

<article class="service" style="left:351px;top:500px">
  <div class="service-photo" role="img" aria-label="Photo of three cleaners in blue shirts dusting a kitchen" style="background:linear-gradient(120deg,#3f7f78,#9fb7b0 45%,#c49e72 80%,#8a5c38)"></div>
  <h3 class="service-name">Deep Cleaning</h3>
  <p class="service-text">Deep cleaning services will be delivered with cleaning materials and equipment and is an open cleaning session with the time allocated based on the level of cleaning as determined by the customer and us. This service is required when you move-in and move-out; or occasional deep cleaning of your residence in an interval of 5 to 6 months which will leave your home lively and refreshing.</p>
  <a class="btn" href="#" style="top:260px">Read More</a>
</article>

<article class="service" style="left:67px;top:802px">
  <div class="service-photo" role="img" aria-label="Photo of a worker operating a floor scrubbing machine on grey tiles" style="background:linear-gradient(135deg,#bdbdbd,#9e9e9e 55%,#8a8a8a)"></div>
  <h3 class="service-name">Commercial Cleaning</h3>
  <p class="service-text">Bedrooms, Kitchen, Bathrooms, Living Areas including Hallways and stairs.On every visit, our LMS team dusts, vacuums, washes and sanitizes each room. Areas on which you want us to focus first and we will work through all areas of your home according to your priority.Booking: We recommend clients to book cleaning services on any fixed days during the week which will be followed every week on the same day and time as per client's request.</p>
  <a class="btn" href="#" style="top:291px">Read More</a>
</article>

<article class="service" style="left:351px;top:802px">
  <div class="service-photo" role="img" aria-label="Photo of a smiling maid in a red apron and yellow gloves" style="background:linear-gradient(180deg,#f4f4f4,#ececec 55%,#e3b0a8 80%,#cf3b2e)"></div>
  <h3 class="service-name">Part-time Maids</h3>
  <p class="service-text">Deep cleaning services will be delivered with cleaning materials and equipment and is an open cleaning session with the time allocated based on the level of cleaning as determined by the customer and us. This service is required when you move-in and move-out; or occasional deep cleaning of your residence in an interval of 5 to 6 months which will leave your home lively and refreshing.Using our equipment and specially formulated products, they clean from left to right, top to bottom, so no detail is overlooked.</p>
  <a class="btn" href="#" style="top:291px">Read More</a>
</article>

<footer class="footer">
  <div class="footer-links">
    <a href="#">Home</a><span class="sep">|</span>
    <a href="#">About Us</a><span class="sep">|</span>
    <a href="#">Services</a><span class="sep">|</span>
    <a href="#">Jobs</a><span class="sep">|</span>
    <a href="#">Maids</a><span class="sep">|</span>
    <a href="#">FAQ's</a><span class="sep">|</span>
    <a href="#">Testimonials</a><span class="sep">|</span>
    <a href="#">Contact Us</a>
  </div>
  <p class="copyright">© 2014 Company Name ,All  Rights Reserved</p>
  <svg class="social" viewBox="0 0 16 16" aria-label="Social link">
    <circle cx="8" cy="8" r="7.2" fill="none" stroke="#ffffff" stroke-width="1"/>
  </svg>
</footer>

</body>
</html>
```